Marbrook Cupcakes Website

We need a new website. We make Texas-size gourmet cupcakes and cupcake jars. We want a website similar to the one KEYlane is hosting and made. They're charging too much per month. I would like to have Blu Otter host it. see the current site at: marbrookcupcakes.com

```html
<!DOCTYPE html>
<html lang="en">
<head>
<meta charset="utf-8">
<title>Marbrook Cupcakes</title>
<link href="https://fonts.googleapis.com/css2?family=Montserrat:ital,wght@0,400;0,500;0,600;0,700;1,400&family=Great+Vibes&display=swap" rel="stylesheet">
<style>
:root{
  --teal:#6fcad3;
  --teal-dark:#49b1bc;
  --teal-deep:#2f9aa6;
  --pale:#e2f3f6;
  --paler:#eef8fa;
  --ink:#222;
  --muted:#666;
  --brown:#3a1d17;
  --white:#fff;
}
*{box-sizing:border-box;margin:0;padding:0}
html,body{width:1200px;height:5348px;overflow:hidden}
body{position:relative;font-family:'Montserrat',sans-serif;color:var(--ink);background:var(--white)}
.abs{position:absolute}
.script{font-family:'Great Vibes',cursive;font-weight:400;color:var(--teal)}
.topbar{left:0;top:0;width:1200px;height:42px;background:var(--teal);color:#fff;font-size:15px;display:flex;justify-content:center;align-items:center;gap:30px}
.topbar b{font-weight:600}
.header{left:0;top:42px;width:1200px;height:103px;background:#fff}
.brand{left:128px;top:28px;font-size:30px;font-weight:600;color:var(--teal-dark);line-height:1}
.brand small{display:block;font-size:16px;font-weight:600;text-align:right;margin-top:2px}
.nav{left:416px;top:66px;display:flex;gap:50px;font-size:14px;font-weight:500}
.nav .on{color:var(--teal-dark)}
.tools{left:808px;top:14px;display:flex;align-items:center;gap:16px;font-size:15px;color:var(--teal-dark)}
.hero{left:0;top:145px;width:1200px;height:449px;background:linear-gradient(100deg,#6b3a1e,#a8683a 45%,#6e3c1f)}
.hero-band{left:60px;top:235px;width:520px;height:215px;background:var(--teal);clip-path:polygon(4% 10%,100% 0,96% 40%,100% 100%,8% 92%,0 60%)}
.hero-text{left:160px;top:270px;width:320px;text-align:center;color:#fff}
.hero-text .l1{font-size:33px;font-weight:500}
.hero-text .l2{font-family:'Great Vibes',cursive;font-size:48px;line-height:1}
.hero-text .l3{font-size:33px;font-weight:500}
.pill-out{display:inline-block;border:2px solid #fff;border-radius:22px;padding:9px 20px;font-size:14px;font-weight:600;color:#fff;margin-top:22px}
.price-badge{left:921px;top:194px;width:124px;height:124px;border-radius:50%;background:var(--teal);border:4px solid #bfe9ed;color:#fff;text-align:center;padding-top:30px}
.price-badge b{display:block;font-size:25px}
.price-badge span{font-size:11px;font-weight:600;line-height:1.1;display:block}
.cats{left:0;top:594px;width:1200px;height:2111px;background:var(--pale)}
.title{left:0;width:1200px;text-align:center;font-size:33px;font-weight:600;letter-spacing:.5px}
.title .script{font-size:82px;margin-right:14px;vertical-align:-10px}
.card{width:297px;height:297px;background:var(--teal);border:6px solid var(--teal)}
.card .img{width:100%;height:210px;background:linear-gradient(160deg,#8d5028,#5c2f18)}
.card .lab{display:flex;justify-content:space-between;align-items:center;color:#fff;font-size:15px;font-weight:600;padding:30px 16px 0}
.btn{display:inline-block;border-radius:24px;font-size:14px;font-weight:600;text-align:center}
.btn-dark{left:471px;top:1476px;width:258px;height:42px;line-height:42px;background:var(--brown);color:#fff}
.banner{left:33px;top:1574px;width:1167px;height:460px;background:var(--teal);border-radius:230px 0 0 230px}
.seal{left:87px;top:1640px;width:333px;height:333px;border-radius:50%;background:#fff;display:flex;align-items:center;justify-content:center}
.seal div{width:220px;height:220px;border-radius:50%;background:linear-gradient(#bfe8ee,#5ab5c2)}
.athlete{left:955px;top:1547px;width:245px;height:623px;background:linear-gradient(#d8f0f3,#b63a2e 50%,#6a3a25);opacity:.85;border-radius:40px 0 0 40px}
.banner-brand{left:440px;top:1660px;width:480px;text-align:center;color:#fff;font-size:64px;font-weight:600;line-height:1}
.banner-brand small{display:block;font-size:31px;font-weight:500;margin:6px 0 0 180px}
.banner-copy{left:446px;top:1794px;width:470px;text-align:center;color:#fff;font-size:16px;line-height:24px}
.prod{width:293px;height:381px;border:8px solid #9fdbe1;background:linear-gradient(#29919c,#6ccad3);color:#fff;text-align:center;padding-top:34px}
.prod h3{font-size:20px;font-weight:600}
.prod p{font-size:14px}
.prod .pr{font-size:24px;font-weight:700;margin-top:2px}
.prod .btn{border:2px solid #fff;padding:4px 14px;margin-top:10px}
.prod .img{width:150px;height:190px;margin:24px auto 0;background:linear-gradient(#a87a4c,#4e2a17);border-radius:60px 60px 10px 10px}
.circ{width:54px;height:54px;border:2px solid #333;border-radius:50%;display:flex;align-items:center;justify-content:center}
.founder{left:0;top:2705px;width:1200px;height:648px;background:var(--paler)}
.fphoto{left:129px;top:2761px;width:380px;height:488px;border-radius:50% 50% 50% 50%/40% 40% 60% 60%;background:linear-gradient(#d7eef1 30%,#3a3a44 70%)}
.ftitle{left:561px;top:2870px;font-size:33px;font-weight:600}
.ftitle .script{font-size:82px;margin-right:14px;vertical-align:-10px}
.fcopy{left:561px;top:2974px;width:480px;font-size:15px;line-height:26.5px}
.btn-teal{background:var(--teal);color:#fff;height:42px;line-height:42px;padding:0 22px}
.flav{width:218px;text-align:center}
.flav .img{height:166px;background:linear-gradient(#7a4525,#e8e0c8)}
.flav h4{font-size:20px;font-weight:500;margin-top:18px}
.flav .pr{color:var(--teal-dark);font-size:20px;font-weight:600;margin-top:6px}
.flav small{color:#999;font-size:12px;display:block}
.quote{left:104px;top:3971px;width:990px;height:285px;background:var(--teal);border-radius:142px;color:#fff;text-align:center}
.quote p{font-style:italic;font-size:18px;line-height:29px;width:610px;margin:80px auto 0}
.quote b{display:block;font-size:20px;margin-top:22px}
.qm{font-size:150px;font-weight:700;line-height:1;color:#fff;opacity:.9;font-family:Georgia,serif}
.insta{top:4445px;width:231px;height:239px}
.footer{left:0;top:4878px;width:1200px;height:470px;background:var(--pale)}
.fhead{font-size:24px;font-weight:600}
.flinks{font-size:13px;line-height:30px;margin-top:12px}
.loc{display:flex;gap:12px;font-size:13px;line-height:19px;margin-top:20px}
.news-in{display:flex;margin-top:18px}
.news-in span{width:167px;height:46px;background:#fff;font-size:13px;padding:15px 10px}
.news-in b{width:120px;height:46px;background:var(--teal);color:#fff;font-size:14px;line-height:46px;text-align:center}
.soc{display:flex;gap:9px;margin-top:16px}
.soc i{width:30px;height:30px;border-radius:50%;background:var(--teal)}
.copy{left:0;top:5258px;width:1200px;text-align:center;font-size:15px}
</style>
</head>
<body>

<div class="abs topbar"><b>Locations:</b><span>&#9679; 2210 Cedar Ave Dallas Texas</span><span>&#9679; 4870 Willow Bend Rd Frisco Texas</span></div>

<header class="abs header">
  <div class="abs brand">Marbrook<small>cupcakes</small></div>
  <nav class="abs nav"><span class="on">HOME</span><span>SHOP ONLINE</span><span>FLOVRS</span><span>ABOUT ME</span><span>BLOG</span><span>LOCATIONS</span></nav>
  <div class="abs tools">
    <span>&#9742; Call: 0815550142</span>
    <svg width="18" height="18" viewBox="0 0 20 20"><circle cx="8" cy="8" r="6" fill="none" stroke="#222" stroke-width="2.5"/><path d="M12 12l6 6" stroke="#222" stroke-width="2.5"/></svg>
    <svg width="18" height="18" viewBox="0 0 20 20"><circle cx="10" cy="6" r="4.5" fill="#222"/><path d="M2 19c0-5 4-7 8-7s8 2 8 7z" fill="#222"/></svg>
    <svg width="22" height="20" viewBox="0 0 22 20"><path d="M1 2h4l3 11h10l2-8H6" fill="none" stroke="#222" stroke-width="2"/><circle cx="9" cy="17" r="2" fill="#222"/><circle cx="17" cy="17" r="2" fill="#222"/></svg>
  </div>
</header>

<section class="abs hero" role="img" aria-label="Cupcake with cream frosting and a strawberry on a glass stand over a wooden table"></section>
<div class="abs hero-band"></div>
<div class="abs hero-text"><div class="l1">SAVE 15% FOR</div><div class="l2">Valentines Day</div><div class="l3">WITH LOVE25</div><span class="pill-out">ONLINE ORDER</span></div>
<div class="abs price-badge"><b>$6.00</b><span>PICK UP &amp;<br>DELIVERY</span></div>

<section class="abs cats"></section>
<h2 class="abs title" style="top:650px"><span class="script">Product</span>CATEGORIES</h2>

<div class="abs card" style="left:129px;top:791px"><div class="img" role="img" aria-label="Gourmet cupcakes with coconut pecan topping"></div><div class="lab">GOURMET CUPCAKES<span>&#10230;</span></div></div>
<div class="abs card" style="left:453px;top:791px"><div class="img" role="img" aria-label="Cupcake jars with whipped frosting"></div><div class="lab">CUPCAKE JARS<span>&#10230;</span></div></div>
<div class="abs card" style="left:774px;top:791px"><div class="img" role="img" aria-label="Wedding cupcake with white frosting"></div><div class="lab">WEDDING CAKES<span>&#10230;</span></div></div>
<div class="abs card" style="left:129px;top:1115px"><div class="img" role="img" aria-label="Cupcake with caramel topping"></div><div class="lab">YOUR FLAVORS<span>&#10230;</span></div></div>
<div class="abs card" style="left:453px;top:1115px"><div class="img" role="img" aria-label="Chocolate frosted cupcake"></div><div class="lab">VALENTINE'S DAY<span>&#10230;</span></div></div>
<div class="abs card" style="left:774px;top:1115px"><div class="img" role="img" aria-label="Assorted birthday cupcakes from above" style="background:linear-gradient(135deg,#f3d9c4,#e26b6b,#f5e6d6)"></div><div class="lab">BIRTHDAY CUPCAKES<span>&#10230;</span></div></div>

<div class="abs btn btn-dark">PICK UP AND DELIVERY</div>

<div class="abs banner"></div>
<div class="abs athlete" role="img" aria-label="Young basketball player in a red jersey leaping with a cupcake held high"></div>
<div class="abs seal" role="img" aria-label="Round seal with a globe and cupcake for the best cupcake on the planet"><div></div></div>
<div class="abs banner-brand">Marbrook<small>cupcakes</small></div>
<p class="abs banner-copy">Lorem ipsum dolor sit amet, consectetur adipiscing elit, sed do eiusmod tempor incididunt ut labore et dolore magna aliqua. Quis ipsum suspendisse ultric es gravida. Risus commodo viverra maecenas accumsan lacus vel facilisis.</p>

<h2 class="abs title" style="top:2100px"><span class="script">Our</span>PRODUCTS</h2>
<div class="abs circ" style="left:50px;top:2384px"><svg width="16" height="16" viewBox="0 0 16 16"><path d="M10 2L4 8l6 6" fill="none" stroke="#333" stroke-width="2"/></svg></div>
<div class="abs circ" style="left:1088px;top:2384px"><svg width="16" height="16" viewBox="0 0 16 16"><path d="M6 2l6 6-6 6" fill="none" stroke="#333" stroke-width="2"/></svg></div>
<div class="abs prod" style="left:137px;top:2219px"><h3>German Chocolate</h3><p>Pick up and Delivery</p><div class="pr">$6.00</div><span class="btn">Online Order</span><div class="img" role="img" aria-label="German chocolate cupcake"></div></div>
<div class="abs prod" style="left:453px;top:2219px"><h3>Caramel Crunch</h3><p>Pick up and Delivery</p><div class="pr">$6.00</div><span class="btn">Online Order</span><div class="img" role="img" aria-label="Caramel crunch cupcake"></div></div>
<div class="abs prod" style="left:769px;top:2219px"><h3>Lemon Cake</h3><p>Pick up and Delivery</p><div class="pr">$6.00</div><span class="btn">Online Order</span><div class="img" role="img" aria-label="Lemon cupcake with white frosting" style="background:linear-gradient(#fff8e0,#e8c24a)"></div></div>

<section class="abs founder"></section>
<div class="abs fphoto" role="img" aria-label="Portrait of the founder in a dark suit"></div>
<h2 class="abs ftitle"><span class="script">Meet</span>FOUNDER</h2>
<p class="abs fcopy">Lorem ipsum dolor sit amet, consectetur adipiscing elit, sed do eiusmod tempor incididunt ut labore et dolore magna aliqua. Quis ipsum suspendisse ultrices gravida. Risus commodo vivea maecenas accumsan lacus vel facilisis. Lorem ipsum dolor sit amet, consectetur adipiscing elit, sed do eiusmod tempor incididunt ut labore et dolore magna aliqua.</p>
<span class="abs btn btn-teal" style="left:567px;top:3155px">FOLLOW ME</span>

<h2 class="abs title" style="top:3432px"><span class="script">Our</span>FLAVORS</h2>
<div class="abs circ" style="left:42px;top:3615px"><svg width="16" height="16" viewBox="0 0 16 16"><path d="M10 2L4 8l6 6" fill="none" stroke="#333" stroke-width="2"/></svg></div>
<div class="abs circ" style="left:1095px;top:3615px"><svg width="16" height="16" viewBox="0 0 16 16"><path d="M6 2l6 6-6 6" fill="none" stroke="#333" stroke-width="2"/></svg></div>
<div class="abs flav" style="left:127px;top:3550px"><div class="img" role="img" aria-label="Carrot cake cupcake"></div><h4>Carrot Cake</h4><div class="pr">$6.00</div><small>Pick up and Delivery</small></div>
<div class="abs flav" style="left:369px;top:3550px"><div class="img" role="img" aria-label="Lemon cupcake" style="background:linear-gradient(#f4e7b5,#f8f4e8)"></div><h4>Lemon</h4><div class="pr">$6.00</div><small>Pick up and Delivery</small></div>
<div class="abs flav" style="left:611px;top:3550px"><div class="img" role="img" aria-label="Chocolate mousse cupcake" style="background:linear-gradient(#e9e6e2,#4a2a1c)"></div><h4>Chocolate Mousse</h4><div class="pr">$6.00</div><small>Pick up and Delivery</small></div>
<div class="abs flav" style="left:853px;top:3550px"><div class="img" role="img" aria-label="Red velvet cupcake" style="background:linear-gradient(#b8352d,#f3ece4)"></div><h4>Red Velvet</h4><div class="pr">$6.00</div><small>Pick up and Delivery</small></div>
<span class="abs btn btn-teal" style="left:386px;top:3853px">ONLINE ORDER</span>
<span class="abs btn btn-teal" style="left:577px;top:3853px">PICK UP AND DELIVERY</span>

<div class="abs quote"><p>Lorem ipsum dolor sit amet, consectetur adipiscing elit, sed do eiusmod tempor incididunt ut labore et dolore magna aliqua. Quis ipsum suspendisse ultrices gravida. Risus commodo viverra maecenas accumsan lacus vel facilisis.</p><b>~Ava Collins</b></div>
<div class="abs qm" style="left:205px;top:4040px">&#8220;</div>
<div class="abs qm" style="left:925px;top:4040px">&#8221;</div>

<h2 class="abs title" style="top:4330px"><span class="script">Follow</span>MARBROOKCUPCAKES</h2>
<div class="abs insta" style="left:0;background:linear-gradient(#f4ede4,#7cc4d0)" role="img" aria-label="Cupcake jars on a display"></div>
<div class="abs insta" style="left:243px;background:linear-gradient(#5fb8c2,#f2e6d6)" role="img" aria-label="Box of assorted cupcakes"></div>
<div class="abs insta" style="left:485px;background:linear-gradient(#3a5a8a,#d9e8f0)" role="img" aria-label="Staff at the bakery counter"></div>
<div class="abs insta" style="left:728px;background:linear-gradient(#4a3a30,#c8a68a)" role="img" aria-label="Cupcakes in a glass display case"></div>
<div class="abs insta" style="left:970px;background:linear-gradient(#f3ede6,#e7a7b5)" role="img" aria-label="Pastel frosted cupcakes"></div>
<span class="abs btn btn-teal" style="left:515px;top:4725px">FOLLOW ME</span>

<svg class="abs" style="left:0;top:4816px" width="1200" height="70" viewBox="0 0 1200 70"><path d="M0 70 C300 0 900 0 1200 70Z" fill="#e2f3f6"/><path d="M60 56 C350 -6 850 -6 1150 48" fill="none" stroke="#6fcad3" stroke-width="5"/></svg>
<footer class="abs footer"></footer>
<div class="abs" style="left:150px;top:4960px;width:186px;height:186px;border-radius:50%;background:radial-gradient(#8fd3dc,#e2f3f6 70%)" role="img" aria-label="Round seal with a globe and cupcake"></div>
<div class="abs" style="left:374px;top:4950px"><div class="fhead">Links</div><div class="flinks">About<br>Reviews<br>Shop<br>Contact Us<br>Blog</div></div>
<div class="abs" style="left:504px;top:4950px"><div class="fhead">Locations</div>
  <div class="loc"><svg width="34" height="34" viewBox="0 0 34 34"><circle cx="17" cy="17" r="17" fill="#6fcad3"/><path d="M17 8a6 6 0 0 0-6 6c0 5 6 12 6 12s6-7 6-12a6 6 0 0 0-6-6z" fill="#fff"/><circle cx="17" cy="14" r="2.2" fill="#6fcad3"/></svg><div>Location 1:<br>2210 Cedar Ave Dallas Texas</div></div>
  <div class="loc"><svg width="34" height="34" viewBox="0 0 34 34"><circle cx="17" cy="17" r="17" fill="#6fcad3"/><path d="M17 8a6 6 0 0 0-6 6c0 5 6 12 6 12s6-7 6-12a6 6 0 0 0-6-6z" fill="#fff"/><circle cx="17" cy="14" r="2.2" fill="#6fcad3"/></svg><div>Location 2:<br>4870 Willow Bend Rd<br>Frisco Texas</div></div>
</div>
<div class="abs" style="left:785px;top:4950px"><div class="fhead">Newsletter</div><p style="font-size:13px;line-height:19px;margin-top:16px;width:290px">Receive access to VIP discounts, new product launches and more.</p>
  <div class="news-in"><span>Email:</span><b>SUBSCRIBE</b></div>
  <div class="soc"><i></i><i></i><i></i><i></i></div>
</div>
<div class="abs" style="left:125px;top:5228px;width:950px;height:1px;background:#b9dfe5"></div>
<p class="abs copy">Copyright &copy; 2025 All rights reserved - Marbrook Cupcakes</p>

</body>
</html>
```